Business card design for a teacher - double sided, sleek design.

My name is Lina and I am an online Arabic language teacher. I am looking for a beautiful business card design for my online teaching business.

The cards will be printed in 85mm x 55mm size.
The card can be either portrait or landscape.

The design should contain my logo on one side and information on the other.

The design needs to be clean and modern. Use of subtle Arabic geometric patterns would be nice. Icons for the social media information on the card should also match the design theme.

My logo font is Consolas, which is a Monospace font.

Business card design should be delivered with editable PSD or EPS files in the handover.

Thanks

Lina

----

Information on the back:

URL: www.speakwithnadia.net [this should stand out more than other details]
Email: info@speakwithnadia.net
Instagram: @speakwithnadia
Facebook: facebook.com/speakwithnadia
Skype: speakwithnadia

My brand colours are shown in the logo attached. These are:
- Teal green - 4DC9C1
- Mango yellow - FFD600

Target Market(s)

- Young professionals
- Expatriates
- Women and Men

Industry/Entity Type

Education

Contact Information for Business Card

Information on the back:

Skype: speakwithnadia

- Teal green - 4DC9C1
- Mango yellow - FFD600

Font styles to use
Other font styles liked:
• Any font complimentary to my logo font which is a Monospace font called Consolas.

Colors

Designer to choose colors to be used in the design.

Requirements
Must have
• - Aesthetically pleasing look
• - Complimentary design with existing logo
Nice to have
• Arabic geometrical patterns

```html
<!DOCTYPE html>
<html lang="en">
<head>
<meta charset="utf-8">
<title>Arabic with Lina – Business Cards</title>
<link rel="stylesheet" href="https://fonts.googleapis.com/css2?family=Roboto:wght@400;700&display=swap">
<style>
  :root {
    --stage: #2a2a2a;
    --card: #ffffff;
    --teal: #4dc9c1;
    --teal-tint: #dff3f2;
    --mango-tint: #fdf6cf;
    --ink: #5a5a5a;
  }
  * { box-sizing: border-box; margin: 0; padding: 0; }
  html, body { width: 1200px; height: 960px; overflow: hidden; }
  body { background: var(--stage); position: relative; font-family: "Roboto", Arial, sans-serif; }

  .card {
    position: absolute; left: 312px; width: 599px; height: 343px;
    background: var(--card); overflow: hidden;
  }
  .card--front { top: 104px; }
  .card--back  { top: 501px; }

  .decoration {
    position: absolute; top: 0; right: 0; width: 365px; height: 100%;
    border-radius: 180px 0 0 160px;
  }
  .card--front .decoration { background: var(--teal-tint); }
  .card--back  .decoration { background: var(--mango-tint); }

  .brand {
    position: absolute; left: 44px; display: flex; align-items: center; gap: 12px;
  }
  .brand__dot { width: 14px; height: 14px; border-radius: 50%; background: var(--teal); flex: none; }
  .brand__name {
    font-weight: 400; font-size: 28px; color: var(--ink);
    letter-spacing: 1px; white-space: nowrap;
  }
  .card--front .brand { top: 68px; }
  .card--back  .brand { top: 112px; }

  .contacts { position: absolute; left: 44px; top: 212px; list-style: none; }
  .contacts li {
    display: flex; align-items: center; gap: 9px;
    font-size: 14px; line-height: 19px; color: var(--ink);
  }
  .contacts svg { width: 12px; height: 12px; flex: none; }

  .website {
    position: absolute; left: 45px; bottom: 42px;
    font-size: 14px; font-weight: 700; letter-spacing: 1.6px; color: var(--ink);
  }
</style>
</head>
<body>

<section class="card card--front" aria-label="Business card, contact side">
  <div class="decoration" role="img" aria-label="Faint large calligraphy decoration in pale teal"></div>
  <div class="brand">
    <span class="brand__dot"></span>
    <span class="brand__name">Arabic with Lina</span>
  </div>
  <ul class="contacts">
    <li>
      <svg viewBox="0 0 12 12" aria-hidden="true"><rect x="0.5" y="2" width="11" height="8" fill="var(--teal)"/><path d="M0.5 2.5 6 6.5 11.5 2.5" fill="none" stroke="#fff" stroke-width="1"/></svg>
      info@speakwithnadia.net
    </li>
    <li>
      <svg viewBox="0 0 12 12" aria-hidden="true"><rect x="0.5" y="0.5" width="11" height="11" rx="1.5" fill="var(--teal)"/></svg>
      @speakwithnadia
    </li>
    <li>
      <svg viewBox="0 0 12 12" aria-hidden="true"><rect x="0.5" y="0.5" width="11" height="11" rx="1.5" fill="var(--teal)"/></svg>
      /speakwithnadia
    </li>
    <li>
      <svg viewBox="0 0 12 12" aria-hidden="true"><circle cx="6" cy="6" r="5.5" fill="var(--teal)"/></svg>
      speakwithnadia
    </li>
    <li>
      <svg viewBox="0 0 12 12" aria-hidden="true"><circle cx="6" cy="6" r="5.5" fill="var(--teal)"/><path d="M0.5 6h11M6 0.5c-2.5 3-2.5 8 0 11M6 0.5c2.5 3 2.5 8 0 11" fill="none" stroke="#fff" stroke-width="0.9"/></svg>
      speakwithnadia.net
    </li>
  </ul>
</section>

<section class="card card--back" aria-label="Business card, brand side">
  <div class="decoration" role="img" aria-label="Faint large calligraphy decoration in pale mango yellow"></div>
  <div class="brand">
    <span class="brand__dot"></span>
    <span class="brand__name">Arabic with Lina</span>
  </div>
  <p class="website">SPEAKWITHNADIA.NET</p>
</section>

</body>
</html>
```